Corvana Tongue Works, LLC

We need a business card that includes information about our business and conveys a reliable business that provides document translation services and interpreters for a variety of corporate and individual clients. We want to come across as professional, reliable, yet approachable. It should include the following on one side:

ESL / ENL Language Classes, Private Lessons, and Online Tutors
PLEXA Training and Testing
Translating & Interpreting Services
Contact us about Over-the-Phone Interpreting in over 200 languages
24/7/365
www.corvanatongue.example

The other side should include (555) 481-3062

Rhoda Pelling, President
482 Garnet Ave., Ste. 219
Indianapolis, IN 40917

Please add USA as part of the address. Also, please add rmpelling@corvanatongueworks.example as the e-mail address. Thank you.

Target Market(s)

Business professionals, their families, the international community

Industry/Entity Type

Business

Contact Information for Business Card

24/7/365
www.corvanatongue.example

(555) 481-3062

Rhoda Pelling, President
482 Garnet Ave., Ste. 219
Indianapolis, IN 40917
USA

Font styles to use
Sans Serif

Colors

Designer to choose colors to be used in the design.

Requirements
Must have
• See project description
• e-mail address and web address
• Phone number
Nice to have
• a globe
• physical address
Should not have
• Should not have the same color scheme as other agencies in our market in Indiana unless it is blue and black. No purple or yellow.

```html
<!DOCTYPE html>
<html lang="en">
<head>
<meta charset="utf-8">
<title>Corvana Tongue Works — Business Card</title>
<link href="https://fonts.googleapis.com/css2?family=Lato:wght@400;700;900&display=swap" rel="stylesheet">
<style>
  :root {
    --stage: #2b2b2b;
    --card-white: #f4f4f4;
    --brand-blue: #2196d6;
    --ink: #111111;
    --ink-soft: #4a4a4a;
    --paper-white: #ffffff;
  }
  * { margin: 0; padding: 0; box-sizing: border-box; }
  html, body { width: 1200px; height: 960px; overflow: hidden; }
  body {
    background: var(--stage);
    font-family: "Lato", Arial, sans-serif;
    position: relative;
  }
  .card {
    position: absolute;
    width: 600px;
    height: 342px;
    border-radius: 18px;
    overflow: hidden;
  }
  /* Front */
  .card-front { left: 302px; top: 129px; background: var(--card-white); }
  .side-band {
    position: absolute; left: 46px; top: 0; width: 69px; height: 342px;
    background: var(--brand-blue);
  }
  .side-band-top {
    position: absolute; left: 0; top: 0; width: 69px; height: 46px;
    background: var(--ink);
  }
  .brand-dot {
    position: absolute; left: 34px; top: 43px; width: 92px; height: 92px;
    border-radius: 50%;
    background: var(--brand-blue);
    border: 5px solid var(--paper-white);
  }
  .brand-name {
    position: absolute; left: 132px; top: 46px;
    font-size: 24px; line-height: 28px; font-weight: 400; color: var(--ink);
  }
  .band-icon { position: absolute; left: 71px; width: 16px; height: 16px; }
  .contact-block {
    position: absolute; left: 133px;
    color: var(--ink-soft); font-size: 14.5px; line-height: 19px; white-space: nowrap;
  }
  .person-name {
    position: absolute; left: 131px; top: 149px;
    font-size: 22px; font-weight: 700; color: var(--brand-blue); letter-spacing: -0.2px;
  }
  .person-title {
    position: absolute; left: 133px; top: 174px;
    font-size: 15px; font-weight: 700; color: var(--ink);
  }
  /* Back */
  .card-back { left: 299px; top: 488px; background: var(--brand-blue); color: var(--paper-white); text-align: center; }
  .world-map {
    position: absolute; left: 20px; top: 10px; width: 560px; height: 330px;
    background: radial-gradient(ellipse at 50% 45%, rgba(255,255,255,0.14), rgba(255,255,255,0.04) 70%, rgba(255,255,255,0) 100%);
  }
  .services { position: absolute; left: 0; right: 0; top: 80px; font-size: 16px; line-height: 19px; }
  .callout { position: absolute; left: 0; right: 0; top: 156px; font-size: 17.5px; line-height: 21px; font-weight: 700; }
  .availability { position: absolute; left: 0; right: 0; top: 216px; font-size: 20px; font-weight: 900; }
  .availability svg { vertical-align: -2px; margin-right: 4px; }
  .web-address { position: absolute; left: 0; right: 0; top: 246px; font-size: 17px; }
  .web-address strong { font-weight: 900; }
</style>
</head>
<body>

<section class="card card-front" aria-label="Business card front">
  <div class="side-band"><div class="side-band-top"></div></div>
  <div class="brand-dot"></div>
  <div class="brand-name">Corvana<br>Tongue<br>Works, LLC</div>

  <svg class="band-icon" style="top:156px" viewBox="0 0 16 16" aria-hidden="true"><circle cx="8" cy="5" r="3.5" fill="#fff"/><path d="M1 15c0-4 3-6 7-6s7 2 7 6z" fill="#fff"/></svg>
  <svg class="band-icon" style="top:201px" viewBox="0 0 16 16" aria-hidden="true"><path d="M8 1a5 5 0 0 0-5 5c0 4 5 9 5 9s5-5 5-9a5 5 0 0 0-5-5z" fill="#fff"/><circle cx="8" cy="6" r="2" fill="var(--brand-blue)"/></svg>
  <svg class="band-icon" style="top:246px" viewBox="0 0 16 16" aria-hidden="true"><path d="M3 1l3 1 1 3-2 1.5c1 2 2.5 3.5 4.5 4.5L11 9l3 1 1 3-2 2C7 15 1 9 1 3z" fill="#fff"/></svg>
  <svg class="band-icon" style="top:266px;height:12px" viewBox="0 0 16 12" aria-hidden="true"><rect x="1" y="1" width="14" height="10" fill="#fff"/><path d="M1 1l7 6 7-6" fill="none" stroke="var(--brand-blue)" stroke-width="1.3"/></svg>
  <svg class="band-icon" style="top:285px" viewBox="0 0 16 16" aria-hidden="true"><circle cx="8" cy="8" r="6.5" fill="#fff"/><path d="M1.5 8h13M8 1.5c-3 3-3 10 0 13M8 1.5c3 3 3 10 0 13" fill="none" stroke="var(--brand-blue)" stroke-width="1"/></svg>

  <div class="person-name">RHODA PELLING</div>
  <div class="person-title">PRESIDENT</div>
  <div class="contact-block" style="top:200px">482 Garnet Ave., Ste. 219<br>Indianapolis, IN 40917 USA</div>
  <div class="contact-block" style="top:245px">(555) 481-3062<br>rmpelling@corvanatongueworks.example<br>www.corvanatongue.example</div>
</section>

<section class="card card-back" aria-label="Business card back">
  <div class="world-map" role="img" aria-label="Faint world map in light blue behind the text"></div>
  <p class="services">ESL / ENL Language Classes, Private Lessons, &amp; Online Tutors<br>PLEXA Training &amp; Testing<br>Translating &amp; Interpreting Services</p>
  <p class="callout">CONTACT US ABOUT OVER-THE-PHONE<br>INTERPRETING IN OVER 200 LANGUAGES</p>
  <p class="availability"><svg width="18" height="18" viewBox="0 0 18 18" aria-hidden="true"><circle cx="9" cy="9" r="7.5" fill="none" stroke="#fff" stroke-width="1.6"/><path d="M9 4v5l-3 3" fill="none" stroke="#fff" stroke-width="1.6"/></svg>24/7/365</p>
  <p class="web-address">www.<strong>CORVANATONGUE</strong>.example</p>
</section>

</body>
</html>
```